Condo Debts Collection Business needs a Web Design (Contest)

I need a site for a client, who works with condo debts collection, and ensure all revenues provided by condo fees will be always available to the building manager of condo on a specific date, regardless of defaults.I have the logo of the companies, and some requirements on layout (kind of slider, menu options, phone number on a noble position, etc).
Updates

Designs look the same

Target Market(s)

I have two targets for this design: - Condominium's building manager. This target is looking for a solution to overdue debts on it's condo. - Residents on condominiums. This target wants to live in a better place, where their neighbors pay their condominium fees on time.

Number of Pages Required

1 page

Requirements
Must have
• - Slider with title, some short text related, a nice image (I prefer happy and/or peaceful family, people doing business, happy friends, and so on).
• - I have a special attention to menu. I'm looking for one I can have a nice effect, more elegant, charming, kind of innovative.
• - Phone number on the top (or clearly visible).
• - Member log in area or icon on the top (or clearly visible).
• - News/articles area.
• - Modern fonts, with good quality, sans-serif on areas where reading is more intensive (prefer Google web-fonts).
• - Colors specified on attached files.
• - Header similar or inspired by the "FILE 3"
Nice to have
• - Clear background color, cause it's better to read larger texts (like articles). Dark backgrounds makes reading difficult.
• - A site with effects (like shadows, lines, gradients, lights) is usually pretty.
• - I pay attention on beautiful footers.
Should not have
• - Images with a lot of money (I don't sell richness, I sell tranquility, peace, harmony, safety).
• - Poor menu.
• - Lots of curves. My customer asked for straight lines.

```html
<!DOCTYPE html>
<html lang="en">
<head>
<meta charset="utf-8">
<title>Serenara — Condo Debt Recovery</title>
<link href="https://fonts.googleapis.com/css2?family=Raleway:wght@400;500;600;700;800&family=Open+Sans:wght@400;600;700&display=swap" rel="stylesheet">
<style>
:root{
  --navy:#142f63;
  --navy-deep:#0d2150;
  --orange:#ee6a25;
  --orange-soft:#f47b2e;
  --ink:#222;
  --muted:#777;
  --light:#f1f1f1;
  --footer:#1c1c1c;
  --white:#fff;
}
*{box-sizing:border-box;margin:0;padding:0}
html,body{width:1200px;height:3448px;overflow:hidden}
body{font-family:"Open Sans",sans-serif;color:var(--ink);background:var(--white);position:relative}
.abs{position:absolute}
a{color:inherit;text-decoration:none}

/* header */
.site-header{position:absolute;left:0;top:0;width:1200px;height:118px;background:var(--navy)}
.brand{left:92px;top:28px;display:flex;align-items:center;gap:12px;color:var(--white);font-family:"Raleway",sans-serif;font-weight:800;font-size:34px;letter-spacing:1px}
.brand-square{width:30px;height:30px;background:var(--orange)}
.top-links{right:92px;top:22px;display:flex;align-items:center;gap:26px;color:var(--white);font-size:17px}
.top-links .sep{width:1px;height:26px;background:rgba(255,255,255,.5)}
.top-links .item{display:flex;align-items:center;gap:9px}
.login{text-decoration:underline}
.toll{font-size:20px}
.main-nav{left:455px;top:80px;height:38px;display:flex;background:var(--orange);border-radius:4px 4px 0 0}
.main-nav a{color:var(--white);font-family:"Raleway",sans-serif;font-weight:600;font-size:14px;padding:0 19px;line-height:38px;border-right:1px solid rgba(255,255,255,.25)}
.main-nav a:last-child{border-right:none}
.main-nav a.active{background:var(--orange-soft);color:#fff6ea}

/* hero */
.hero{left:0;top:118px;width:1200px;height:617px;background:linear-gradient(180deg,#8c8aa0 0%,#7a6b55 35%,#5d5a3a 70%,#3f5a2a 100%)}
.hero-title{left:0;top:275px;width:1200px;text-align:center;color:var(--white);font-family:"Raleway",sans-serif;font-weight:800;font-size:104px;letter-spacing:2px;text-shadow:0 3px 10px rgba(0,0,0,.3)}
.hero-sub{left:0;top:372px;width:1200px;text-align:center;color:var(--white);font-family:"Raleway",sans-serif;font-size:22px}
.hero-dots{left:540px;top:540px;display:flex;gap:16px}
.hero-dots span{width:15px;height:15px;border-radius:50%;background:var(--white);border:2px solid var(--white)}
.hero-dots span.off{background:transparent}

/* service strip */
.service-strip{left:0;top:735px;width:1200px;height:123px;background:var(--orange)}
.strip-item{top:33px;display:flex;gap:16px;color:var(--white);align-items:center}
.strip-num{font-family:"Raleway",sans-serif;font-weight:700;font-size:44px}
.strip-label{font-family:"Raleway",sans-serif;font-weight:500;font-size:21px;line-height:30px;text-transform:uppercase}
.strip-divider{top:35px;width:1px;height:55px;background:rgba(255,255,255,.4)}
.service-col{top:890px;width:300px}
.service-col p{font-size:15px;line-height:28px;color:var(--muted)}
.btn{display:inline-block;background:var(--navy);color:var(--white);font-family:"Raleway",sans-serif;font-weight:700;font-size:16px;padding:0 26px;line-height:38px;border-radius:3px;box-shadow:0 2px 4px rgba(0,0,0,.3)}
.service-col .btn{margin-top:25px}

/* what we do */
.what-we-do{left:0;top:1190px;width:1200px;height:490px;background:linear-gradient(120deg,var(--orange) 0%,var(--orange) 25%,#8a4a40 55%,var(--navy-deep) 80%,var(--navy-deep) 100%)}
.section-title{width:1200px;left:0;text-align:center;font-family:"Raleway",sans-serif;font-weight:500;font-size:44px}
.what-we-do .section-title{top:115px;color:var(--white)}
.what-text{left:150px;top:195px;width:900px;text-align:center;color:var(--white);font-size:15px;line-height:30px}
.what-actions{left:0;top:318px;width:1200px;display:flex;justify-content:center;gap:22px}
.btn-outline{background:var(--white);color:var(--navy);border:2px solid var(--navy)}

/* features */
.feature{width:360px}
.feature h3{display:flex;align-items:center;gap:14px;font-family:"Raleway",sans-serif;font-weight:600;font-size:22px;color:#333;margin-bottom:16px}
.feature p{font-size:14.5px;line-height:28px;color:var(--muted);text-align:justify}
.feature p a{color:var(--navy);font-weight:600}
.feature-mark{left:470px;top:1885px;width:260px;height:140px;display:flex;align-items:center;justify-content:center;gap:14px;color:var(--navy);font-family:"Raleway",sans-serif;font-weight:800;font-size:34px}
.feature-mark .sq{width:36px;height:36px;background:var(--orange)}

/* articles */
.articles{left:0;top:2280px;width:1200px;height:785px;background:var(--light)}
.articles .section-title{top:115px;color:#111}
.article{top:205px;width:322px}
.article-photo{width:322px;height:210px;position:relative}
.article-date{position:absolute;left:10px;bottom:0;width:165px;height:32px;display:flex;align-items:center;justify-content:center;gap:8px;color:var(--white);font-size:12px;font-weight:600}
.article h4{margin-top:52px;font-family:"Raleway",sans-serif;font-weight:700;font-size:19px;color:#111}
.article-meta{margin-top:12px;display:flex;gap:28px;font-size:12px;color:#444;font-weight:600}
.article-meta span{display:flex;align-items:center;gap:6px}
.article p{margin:22px 10px 0;font-size:14.5px;line-height:28px;color:var(--muted)}
.article .more{display:block;margin-top:24px;font-size:14px;font-weight:700;color:var(--navy)}

/* footer */
.site-footer{left:0;top:3065px;width:1200px;height:383px;background:var(--footer);color:#ddd}
.socials{left:78px;top:50px;display:flex;gap:18px}
.socials span{width:18px;height:18px;border-radius:50%;border:2px solid #ddd}
.to-top{left:588px;top:50px}
.subscribe{left:800px;top:35px;display:flex}
.subscribe .field{width:270px;height:44px;background:var(--white);color:#888;font-size:14px;line-height:44px;padding-left:16px}
.subscribe .go{width:54px;height:44px;background:var(--orange);display:flex;align-items:center;justify-content:center}
.contact{top:205px;text-align:center;font-size:13.5px;line-height:22px;color:#ddd}
.contact svg{display:block;margin:0 auto 10px}
.contact-line{top:302px;height:1px;background:#333}
.copyright{left:0;top:338px;width:1200px;text-align:center;font-size:11.5px;color:#ccc}
</style>
</head>
<body>

<header class="site-header">
  <div class="abs brand"><span class="brand-square"></span>SERENARA</div>
  <div class="abs top-links">
    <span class="item login">
      <svg width="20" height="20" viewBox="0 0 20 20"><circle cx="10" cy="10" r="9" fill="none" stroke="#fff" stroke-width="2"/><circle cx="10" cy="8" r="3" fill="#fff"/><path d="M4.5 15.5c1.5-3 9.5-3 11 0" fill="#fff"/></svg>
      Member Login
    </span>
    <span class="sep"></span>
    <span class="item toll">
      <svg width="18" height="18" viewBox="0 0 24 24"><path fill="#fff" d="M6.6 10.8a15.2 15.2 0 0 0 6.6 6.6l2.2-2.2c.3-.3.7-.4 1-.2 1.1.4 2.3.6 3.6.6.6 0 1 .4 1 1V20c0 .6-.4 1-1 1A17 17 0 0 1 3 4c0-.6.4-1 1-1h3.5c.6 0 1 .4 1 1 0 1.3.2 2.5.6 3.6.1.3 0 .7-.2 1z"/></svg>
      Toll Free : 3029-5180
    </span>
  </div>
  <nav class="abs main-nav">
    <a class="active" href="#">HOME</a><a href="#">ABOUT US</a><a href="#">SERVICES</a><a href="#">WHO WE SERVE</a><a href="#">RATES</a><a href="#">CONTACT US</a>
  </nav>
</header>

<section class="abs hero" role="img" aria-label="Photo of a happy family blowing soap bubbles outdoors on the grass">
  <h1 class="abs hero-title">SERENARA</h1>
  <p class="abs hero-sub">Condomínio Em Dia, Vida Em Paz</p>
  <div class="abs hero-dots"><span class="off"></span><span></span><span></span><span></span></div>
</section>

<section class="abs service-strip">
  <div class="abs strip-item" style="left:90px"><span class="strip-num">01</span><span class="strip-label">Commercial<br>Debt Recovery</span></div>
  <div class="abs strip-divider" style="left:412px"></div>
  <div class="abs strip-item" style="left:455px"><span class="strip-num">02</span><span class="strip-label">Legal Debt<br>Recovery</span></div>
  <div class="abs strip-divider" style="left:778px"></div>
  <div class="abs strip-item" style="left:820px"><span class="strip-num">03</span><span class="strip-label">On-Line Stat/<br>Placement</span></div>
</section>

<div class="abs service-col" style="left:92px"><p>Lorem ipsum dolor sit amet, consectetur ing elit, sed do eiusmod tempor incididunt ut labore et dolore magna aliqua. Ut enim ad minim veniam...</p><a class="btn" href="#">Read More</a></div>
<div class="abs service-col" style="left:457px"><p>Lorem ipsum dolor sit amet, consectetur ing elit, sed do eiusmod tempor incididunt ut labore et dolore magna aliqua. Ut enim ad minim veniam...</p><a class="btn" href="#">Read More</a></div>
<div class="abs service-col" style="left:822px"><p>Lorem ipsum dolor sit amet, consectetur ing elit, sed do eiusmod tempor incididunt ut labore et dolore magna aliqua. Ut enim ad minim veniam...</p><a class="btn" href="#">Read More</a></div>

<section class="abs what-we-do">
  <h2 class="abs section-title">What We Do</h2>
  <p class="abs what-text">Lorem ipsum dolor sit amet, consectetur adipiscing elit, sed do eiusmod tempor incididunt ut labore et dolore magna aliqua. Ut enim ad minim veniam, quis nostrud exercitation ullamco laboris nisi ut aliquip ex ea commodo consequat. Duis aute irure dolor in reprehenderit in voluptate velit esse cillum dolore eu fugiat nulla pariatur.</p>
  <div class="abs what-actions"><a class="btn" href="#">Read More</a><a class="btn btn-outline" href="#">Contact Now</a></div>
</section>

<div class="abs feature" style="left:92px;top:1800px">
  <h3><svg width="26" height="26" viewBox="0 0 24 24"><rect x="2" y="5" width="16" height="16" fill="none" stroke="#ee6a25" stroke-width="2"/><path d="M9 14l1-4 9-9 3 3-9 9z" fill="#ee6a25"/></svg>Request For A Free Quote</h3>
  <p>Sed ut perspiciatis unde omnis iste natus error sit voluptatem remque dantium, totam rem aperiam, eaque ipsa quae...<a href="#">Read More ›</a></p>
</div>
<div class="abs feature" style="left:780px;top:1800px">
  <h3><svg width="26" height="26" viewBox="0 0 24 24"><rect x="2" y="3" width="18" height="18" fill="none" stroke="#ee6a25" stroke-width="2"/><path d="M6 12l4 4 11-11" fill="none" stroke="#ee6a25" stroke-width="3"/></svg>Why Choose Us</h3>
  <p>Sed ut perspiciatis unde omnis iste natus error sit voluptatem remque dantium, totam rem aperiam, eaque ipsa quae...<a href="#">Read More ›</a></p>
</div>
<div class="abs feature-mark"><span class="sq"></span>SERENARA</div>
<div class="abs feature" style="left:92px;top:2038px">
  <h3><svg width="24" height="26" viewBox="0 0 24 26"><circle cx="12" cy="7" r="6" fill="#ee6a25"/><path d="M1 26c0-8 22-8 22 0z" fill="#ee6a25"/></svg>Client Registration</h3>
  <p>Sed ut perspiciatis unde omnis iste natus error sit voluptatem remque dantium, totam rem aperiam, eaque ipsa quae...<a href="#">Read More ›</a></p>
</div>
<div class="abs feature" style="left:780px;top:2038px">
  <h3><svg width="26" height="26" viewBox="0 0 24 24"><circle cx="12" cy="12" r="7" fill="none" stroke="#ee6a25" stroke-width="5" stroke-dasharray="3 2.5"/><circle cx="12" cy="12" r="5" fill="#ee6a25"/><circle cx="12" cy="12" r="2" fill="#fff"/></svg>How It Works</h3>
  <p>Sed ut perspiciatis unde omnis iste natus error sit voluptatem remque dantium, totam rem aperiam, eaque ipsa quae...<a href="#">Read More ›</a></p>
</div>

<section class="abs articles">
  <h2 class="abs section-title">Articles</h2>
  <article class="abs article" style="left:90px">
    <div class="article-photo" role="img" aria-label="Photo of hands typing on a laptop keyboard" style="background:linear-gradient(135deg,#c9d3e2,#7d8ba3)">
      <span class="article-date" style="background:var(--orange)">▣ JULY,9 2018</span>
    </div>
    <h4>SED UT PERSPICIATIS UNDE</h4>
    <div class="article-meta"><span>● KATEGREEN</span><span>▪ 45</span></div>
    <p>Duis aute irure dolor in reprehenderit in voluptate velit esse cillum dolore eu fugiat nulla pariatur. Excepteur sint occaecat</p>
    <a class="more" href="#">Read More ›</a>
  </article>
  <article class="abs article" style="left:439px">
    <div class="article-photo" role="img" aria-label="Photo of two smiling friends embracing" style="background:linear-gradient(135deg,#d9b58a,#8a6a4d)">
      <span class="article-date" style="background:var(--navy)">▣ JULY,9 2018</span>
    </div>
    <h4>SED UT PERSPICIATIS UNDE</h4>
    <div class="article-meta"><span>● KATEGREEN</span><span>▪ 45</span></div>
    <p>Duis aute irure dolor in reprehenderit in voluptate velit esse cillum dolore eu fugiat nulla pariatur. Excepteur sint occaecat</p>
    <a class="more" href="#">Read More ›</a>
  </article>
  <article class="abs article" style="left:788px">
    <div class="article-photo" role="img" aria-label="Photo of a family walking on a beach at sunset" style="background:linear-gradient(180deg,#f1a25a,#c9653a 60%,#4a2a26)">
      <span class="article-date" style="background:var(--orange)">▣ JULY,9 2018</span>
    </div>
    <h4>SED UT PERSPICIATIS UNDE</h4>
    <div class="article-meta"><span>● KATEGREEN</span><span>▪ 45</span></div>
    <p>Duis aute irure dolor in reprehenderit in voluptate velit esse cillum dolore eu fugiat nulla pariatur. Excepteur sint occaecat</p>
    <a class="more" href="#">Read More ›</a>
  </article>
</section>

<footer class="abs site-footer">
  <div class="abs socials"><span></span><span></span><span></span><span></span></div>
  <svg class="abs to-top" width="20" height="20" viewBox="0 0 20 20"><path d="M4 10l6-6 6 6M4 16l6-6 6 6" fill="none" stroke="#ee6a25" stroke-width="2"/></svg>
  <div class="abs subscribe"><span class="field">Email Id</span><span class="go"><svg width="22" height="22" viewBox="0 0 24 24"><path d="M2 11l20-9-8 20-3-8z" fill="#fff"/></svg></span></div>

  <div class="abs contact" style="left:80px;width:280px;top:228px">
    <svg width="22" height="18" viewBox="0 0 22 18"><rect x="1" y="1" width="20" height="16" fill="none" stroke="#ddd" stroke-width="2"/><path d="M1 2l10 8 10-8" fill="none" stroke="#ddd" stroke-width="2"/></svg>
    contact@serenara.example
  </div>
  <div class="abs contact" style="left:400px;width:400px;top:205px">
    <svg width="16" height="22" viewBox="0 0 16 22"><path d="M8 1a7 7 0 0 1 7 7c0 5-7 13-7 13S1 13 1 8a7 7 0 0 1 7-7z" fill="#ddd"/><circle cx="8" cy="8" r="2.5" fill="#1c1c1c"/></svg>
    Rua das Palmeiras,140,Centro Empresarial<br>Horizonte,sala 512-Jardim Azul-Vila Nova-SC,CEP 88000-000
  </div>
  <div class="abs contact" style="left:840px;width:280px;top:228px">
    <svg width="20" height="20" viewBox="0 0 24 24"><path fill="#ddd" d="M6.6 10.8a15.2 15.2 0 0 0 6.6 6.6l2.2-2.2c.3-.3.7-.4 1-.2 1.1.4 2.3.6 3.6.6.6 0 1 .4 1 1V20c0 .6-.4 1-1 1A17 17 0 0 1 3 4c0-.6.4-1 1-1h3.5c.6 0 1 .4 1 1 0 1.3.2 2.5.6 3.6.1.3 0 .7-.2 1z"/></svg>
    3029-5170/3029-5180
  </div>
  <div class="abs contact-line" style="left:80px;width:280px"></div>
  <div class="abs contact-line" style="left:840px;width:280px"></div>
  <p class="abs copyright">© 2019 Copyrights.The Company Name.All Rights Reserved</p>
</footer>

</body>
</html>
```